Residential & commercial cleaning business

Looking for Brazilian colors, green/blue/yellow.
Name of business is “Marlowe’s Cleaning”.
Second side of card will be for ‘confirming customer next appointment date/time.
Want to include in description…residential & commercial cleaning, experienced, highly recommended, reasonable rates, free estimates, Marlowe’sCleaningCo@brightmop.net, Fairbrook, NH, Call today at 555.218.6094.

```html
<!DOCTYPE html>
<html lang="en">
<head>
<meta charset="utf-8">
<title>Marlowe’s Cleaning – Business Card</title>
<link href="https://fonts.googleapis.com/css2?family=Montserrat:wght@400;500;600;700&family=Great+Vibes&display=swap" rel="stylesheet">
<style>
  :root {
    --backdrop: #505050;
    --sky: #16a2d6;
    --sun: #fae000;
    --leaf: #5e9a2e;
    --paper: #ffffff;
  }
  * { box-sizing: border-box; margin: 0; padding: 0; }
  html, body { width: 1200px; height: 1200px; overflow: hidden; }
  body {
    background: var(--backdrop);
    position: relative;
    font-family: "Montserrat", sans-serif;
  }
  .card {
    position: absolute;
    left: 186px;
    width: 828px;
    height: 460px;
    overflow: hidden;
    background: var(--sky);
  }
  .card--front { top: 112px; }
  .card--back { top: 628px; }
  .card__shapes { position: absolute; inset: 0; width: 828px; height: 460px; }

  .services {
    position: absolute;
    left: 67px;
    top: 72px;
    color: var(--leaf);
    font-size: 35px;
    line-height: 35px;
    font-weight: 500;
  }
  .brand {
    position: absolute;
    left: 400px;
    top: 100px;
    width: 330px;
    text-align: center;
    color: var(--leaf);
    font-size: 40px;
    line-height: 46px;
    font-weight: 600;
  }
  .call-label {
    position: absolute;
    left: 52px;
    width: 306px;
    top: 284px;
    text-align: center;
    color: var(--paper);
    font-size: 29px;
    font-weight: 700;
  }
  .phone-pill {
    position: absolute;
    left: 52px;
    top: 328px;
    width: 306px;
    height: 82px;
    border-radius: 41px;
    background: var(--sun);
    color: var(--leaf);
    font-size: 35px;
    font-weight: 700;
    display: flex;
    align-items: center;
    justify-content: center;
    letter-spacing: 1px;
  }

  .appointment-title {
    position: absolute;
    left: 0;
    width: 848px;
    top: 46px;
    text-align: center;
    color: var(--leaf);
    font-family: "Great Vibes", cursive;
    font-size: 88px;
    line-height: 100px;
  }
  .field {
    position: absolute;
    height: 64px;
    border: 2px solid var(--leaf);
    border-radius: 32px;
    background: var(--paper);
    color: var(--leaf);
    font-size: 22px;
    font-weight: 600;
    display: flex;
    align-items: center;
    padding-left: 26px;
  }
  .field--date { left: 68px; top: 182px; width: 324px; }
  .field--time { left: 433px; top: 182px; width: 322px; }
  .field--details { left: 68px; top: 268px; width: 687px; }
  .contact {
    position: absolute;
    left: 0;
    width: 828px;
    top: 342px;
    text-align: center;
    color: var(--paper);
    font-size: 24px;
    line-height: 34px;
    font-weight: 500;
  }
</style>
</head>
<body>

<section class="card card--front">
  <svg class="card__shapes" viewBox="0 0 1036 576" aria-hidden="true">
    <path d="M-30,-30 H935 C1015,60 1025,250 995,365 C965,455 880,478 800,468 C650,452 520,330 300,322 C170,318 60,360 -30,410 Z"
          fill="#ffffff" stroke="#fae000" stroke-width="22"/>
    <path id="tagline-curve" d="M92,298 C300,238 500,300 640,362 C720,398 790,422 862,430" fill="none"/>
    <text font-family="Montserrat, sans-serif" font-size="17" font-weight="500" fill="#5e9a2e" letter-spacing="1">
      <textPath href="#tagline-curve">EXPERIENCED · HIGHLY RECOMMENDED · REASONABLE RATES · FREE ESTIMATES</textPath>
    </text>
  </svg>
  <div class="services">Residential<br>&amp; Commercial<br>cleaning</div>
  <div class="brand">Marlowe’s<br>Cleaning</div>
  <div class="call-label">Call today at</div>
  <div class="phone-pill">555.218.6094</div>
</section>

<section class="card card--back">
  <svg class="card__shapes" viewBox="0 0 1036 576" aria-hidden="true">
    <path d="M110,-30 H1070 V318 C980,262 870,215 760,215 C620,215 500,290 380,350 L90,355 C20,250 20,60 110,-30 Z"
          fill="#ffffff" stroke="#fae000" stroke-width="22"/>
  </svg>
  <div class="appointment-title">Your next Appointment</div>
  <div class="field field--date">Date:</div>
  <div class="field field--time">Time:</div>
  <div class="field field--details">Details:</div>
  <div class="contact">Fairbrook, NH<br>Marlowe’sCleaningCo@brightmop.net</div>
</section>

</body>
</html>
```